Garlic Farm for Farm Sales/Restaurant sales

Need a professional, but appealing to agriculture world. We are selling 27 kinds of Organic Garlic from a farm in Simla,CO. I have uploaded logo and business information-we are going to need a template, because I will need to use it for four separate people.
-We are trying to appeal to Farm to table restaurants
-As well as growers/farmers

Target Market(s)

Agriculture Sales/Restaurants-Organic

Industry/Entity Type

Agriculture

Contact Information for Business Card

Want it to look more unique then your average kelto stock card- I want it to look amazing

Font styles to use
Sans Serif

Colors
0455a3
ec1f27
fbed22
ffffff

Requirements
Must have
• Just be creative
Nice to have
• Colorful
Should not have
• plain

```html
<!DOCTYPE html>
<html lang="en">
<head>
<meta charset="utf-8">
<title>Prairie Crest Garlic – Business Card</title>
<link rel="stylesheet" href="https://fonts.googleapis.com/css2?family=Open+Sans:wght@400;600;700;800&display=swap">
<style>
  :root {
    --brand-blue: #0455a3;
    --brand-navy: #233a80;
    --brand-red: #ec1f27;
    --card-red: #c8243a;
    --back-red-light: #e0525a;
    --back-red-dark: #c53a42;
    --brand-yellow: #fbed22;
    --paper: #ffffff;
    --stage: #ece8e2;
    --rule-red: #f08a8f;
  }
  * { box-sizing: border-box; margin: 0; padding: 0; }
  html, body { width: 1200px; height: 780px; overflow: hidden; }
  body {
    background: var(--stage);
    font-family: "Open Sans", Arial, sans-serif;
    display: flex;
    align-items: center;
    justify-content: center;
    gap: 100px;
  }
  .card {
    width: 400px;
    height: 700px;
    border-radius: 22px;
    overflow: hidden;
    position: relative;
    box-shadow: 0 6px 18px rgba(0,0,0,0.15);
  }

  /* Front */
  .card-front { background: var(--paper); display: flex; flex-direction: column; }
  .front-body { flex: 1; padding: 70px 44px 0; display: flex; flex-direction: column; align-items: center; }
  .brand { display: flex; flex-direction: column; align-items: center; gap: 14px; }
  .brand-mark {
    width: 96px; height: 96px; border-radius: 50%;
    background: var(--brand-red);
    border: 4px solid var(--brand-navy);
  }
  .brand-name {
    color: var(--brand-navy);
    font-weight: 800;
    font-size: 36px;
    letter-spacing: 0.5px;
    line-height: 1;
  }
  .person-name {
    margin-top: 40px;
    color: var(--brand-navy);
    font-weight: 800;
    font-size: 30px;
    letter-spacing: 3px;
    text-transform: uppercase;
  }
  .contact-list { margin-top: 30px; width: 100%; list-style: none; }
  .contact-item {
    text-align: center;
    padding: 12px 0;
    border-top: 1px solid var(--rule-red);
  }
  .contact-item:first-child { border-top: none; }
  .contact-label {
    display: block;
    color: var(--brand-red);
    font-weight: 700;
    font-size: 15px;
  }
  .contact-value {
    display: block;
    color: var(--brand-navy);
    font-size: 21px;
    letter-spacing: 1px;
  }
  .front-band {
    height: 110px;
    background: var(--card-red);
    border-top: 6px solid var(--paper);
    box-shadow: 0 -2px 0 var(--brand-blue);
    display: flex; align-items: center; justify-content: center;
  }
  .website { color: var(--paper); font-size: 24px; letter-spacing: 1.5px; }

  /* Back */
  .card-back { color: var(--brand-navy); }
  .back-art {
    position: absolute; inset: 0;
    background: radial-gradient(circle at 60% 40%, var(--back-red-light), var(--back-red-dark));
  }
  .back-content {
    position: relative;
    height: 100%;
    display: flex; flex-direction: column; align-items: center; justify-content: center;
    gap: 26px;
  }
  .back-mark {
    width: 130px; height: 130px; border-radius: 50%;
    background: var(--brand-red);
    border: 5px solid var(--brand-navy);
  }
  .back-name {
    text-align: center;
    font-weight: 700;
    font-size: 30px;
    line-height: 1.25;
    color: var(--brand-navy);
  }
  .social-list { display: flex; gap: 10px; list-style: none; }
  .social-list li {
    width: 30px; height: 30px; border-radius: 4px;
    background: var(--brand-yellow);
  }
</style>
</head>
<body>

  <article class="card card-front">
    <div class="front-body">
      <div class="brand">
        <span class="brand-mark"></span>
        <span class="brand-name">Prairie Crest</span>
      </div>
      <h1 class="person-name">Lena Marsh</h1>
      <ul class="contact-list">
        <li class="contact-item">
          <span class="contact-label">Phone</span>
          <span class="contact-value">555-014-2290</span>
        </li>
        <li class="contact-item">
          <span class="contact-label">Email</span>
          <span class="contact-value">Lena@PCGarlic.com</span>
        </li>
        <li class="contact-item">
          <span class="contact-label">Address</span>
          <span class="contact-value">P.O. Box 48 Dalton, CO 80000</span>
        </li>
      </ul>
    </div>
    <footer class="front-band">
      <span class="website">PCGarlic.com</span>
    </footer>
  </article>

  <article class="card card-back">
    <div class="back-art" role="img" aria-label="Soft red-toned photograph of garlic bulbs and cloves"></div>
    <div class="back-content">
      <span class="back-mark"></span>
      <h2 class="back-name">Prairie Crest<br>Garlic, LLC</h2>
      <ul class="social-list" aria-label="Social channels">
        <li></li><li></li><li></li><li></li>
      </ul>
    </div>
  </article>

</body>
</html>
```